Website for Barlow Fabrication & Building Ltd

General Note to all.

1. Piling and gas works are separate areas of work and should not be put together.
- the marine section should really be the piling works and should have all the barges/water piles etc.
- the gas section should have the big silo looking thing

2. I would like to add in Specialist Onsite Labour and Management in the 'our services' section. The would include the Supervisors, Coded Welders, Site Fitters and Crane and Rig Crews etc.

3. I did like it how someone had use the BFB header logo as the top of the webpage with the individual tabs above and the website starting below. Please remove the VAT number and phone number from this section.

4. I also liked how one designer incorporate the orange line with spark (from the logo) as a page separator representing the welding part of the business

5. Add in a Mission Statement - To go above and beyond in to ensure our clients projects are delivered safely, ahead of schedule, in any environment for the benefit of not only our customers but also our employees and communities we work in.

6. Add in Business Objectives -BFB is on a mission to be one of the leading contractors in UK to supply All Site Labour - ranging from Site Management, fully Coded Welders, Site Fitters and Crane and Rig Crews.

7. I am happy for you to add in photos that are not ours for the thumbs nails for the our services. ie a colourful welding pics/cool tunnelling pic etc - just make sure I will not get done for copy write infringements

8. I would like a some type of 'contact us' field or 'request a consultation' section.

9. Please confirm if the webpages you create will be compatible for both desktop and mobile app and how difficult it will be to update personally once it is live.

10. You have all done very well and have thus far been very impressed with what you have produced. I gave a very vague brief as I was not entirely sure how you would go about making something with very little information. Some of the designs look very professional.

11. I'm not sure how once I choose the winning design how that then transfers over to my domain? Perhaps someone can help me with that? I will also be looking for a web hosting platform so feel free to provide this information.

After using Sketch hive for successful getting a professional logo for the company I'm giving the web design option a go.

I am looking for a professional website for the above civil construction company.

The company director has many years experience in Marine, tunnelling, conveyors, stadium construction gas and piling works including piling works for coal ports, bridges and tunnels.

The company currently provide 20+ skilled and experienced guys from all trades (supervisors, coded welders, fitters, crane drivers and crane supervisors, rigglers, slingers and piling operatives) on the Corran Shoreline project in London - London's new super sewer. Most of this work is off barges carrying cranes (upto 600T and drill rigs).

As we are looking to expand and get more subcontracts we need a web presence to say who we are and what we do.

I'll include the 2 company logos we currently use below

I have included an info doc with pics you may or may not use.

Target Market(s)

Mainly other large construction companies and potential subcontractors

Industry/Entity Type

Construction Company

Coding

Coded - Design and coding required

Font styles to use
Sans Serif

Colors
0655a3
f37122
ffffff

Requirements
Must have
• Few tabs
• Simple to use/update but still professional look
• The challenge will be making the website look professional with not much available content.
Should not have
• No residential house building

```html
<!DOCTYPE html>
<html lang="en">
<head>
<meta charset="utf-8">
<title>Barlow Fabrication &amp; Building</title>
<link href="https://fonts.googleapis.com/css2?family=Montserrat:wght@400;500;600;700&display=swap" rel="stylesheet">
<style>
:root{
  --blue:#0655a3;
  --orange:#f37122;
  --orange-light:#f58634;
  --orange-dark:#e4621a;
  --white:#ffffff;
  --ink:#333333;
  --grey:#f1f1f1;
  --dark:#2b2b2b;
}
*{box-sizing:border-box;margin:0;padding:0}
html,body{width:1200px;height:3429px;overflow:hidden}
body{font-family:'Montserrat',sans-serif;color:var(--ink);background:var(--white);position:relative}
.abs{position:absolute}
a{color:inherit;text-decoration:none}

/* header */
.site-header{position:absolute;left:0;top:0;width:1200px;height:130px}
.brand{position:absolute;left:98px;top:22px;display:flex;align-items:center;gap:10px}
.brand-mark{width:34px;height:34px;border-radius:50%;background:var(--orange)}
.brand-name{font-weight:700;font-size:30px;color:var(--blue);letter-spacing:1px;line-height:1}
.brand-sub{font-weight:600;font-size:11px;color:var(--blue);letter-spacing:1px;margin-top:4px}
.topbar{position:absolute;left:400px;top:0;width:800px;height:58px;background:var(--blue);clip-path:polygon(24px 0,100% 0,100% 100%,0 100%);display:flex;justify-content:flex-end;align-items:center;gap:36px;padding-right:100px;color:var(--white);font-size:15px;font-weight:500}
.topbar span{display:flex;align-items:center;gap:8px}
.mainnav{position:absolute;left:340px;top:58px;width:860px;height:62px;background:var(--orange);clip-path:polygon(24px 0,100% 0,100% 100%,0 100%);display:flex;align-items:center;justify-content:flex-end;gap:42px;padding-right:100px;color:var(--white);font-size:15px;font-weight:600}

/* hero */
.hero{position:absolute;left:0;top:130px;width:1200px;height:550px}
.hero-photo{position:absolute;inset:0;background:linear-gradient(180deg,#4a6d97 0%,#6f8db0 40%,#5d5a55 75%,#3c3a36 100%)}
.hero h1{position:absolute;right:98px;top:100px;width:700px;text-align:right;color:var(--white);font-size:44px;font-weight:700;line-height:1.1}
.hero p{position:absolute;right:98px;top:218px;width:640px;text-align:right;color:var(--white);font-size:18px;font-weight:500;line-height:1.6}
.btn{display:inline-block;border:2px solid var(--white);color:var(--white);font-size:15px;font-weight:600;padding:13px 20px}
.hero .btn{position:absolute;right:98px;top:305px}
.hero-arrow{position:absolute;top:210px}

/* about */
.eyebrow{font-size:15px;font-weight:600;color:var(--blue);letter-spacing:1px}
.section-title{font-size:28px;font-weight:700;color:var(--orange);letter-spacing:.5px}
.rule{width:80px;height:3px;background:var(--orange)}
.about{position:absolute;left:100px;top:760px;width:1000px}
.about-text{position:absolute;left:0;top:100px;width:602px;font-size:13.4px;line-height:1.8}
.about-text p+p{margin-top:16px}
.about-photo{position:absolute;left:625px;top:20px;width:375px;height:285px;background:linear-gradient(180deg,#8fb2d4 0%,#b8cde0 45%,#5d7085 62%,#37485a 100%)}
.about-bar{position:absolute;left:650px;width:325px;height:12px;background:#4a4a4a}

/* services */
.services{position:absolute;left:0;top:1170px;width:1200px;height:282px;display:flex}
.service{width:400px;padding:38px 30px 0 98px;color:var(--white);position:relative}
.service:nth-child(1){background:var(--orange)}
.service:nth-child(2){background:var(--orange-light)}
.service:nth-child(3){background:var(--orange-dark)}
.service-icon{position:absolute;left:24px;top:38px}
.service h3{font-size:22px;font-weight:500;line-height:1.3}
.service h3 b{font-weight:700}
.service p{font-size:13.4px;line-height:1.7;margin-top:14px;width:280px}
.service .btn{margin-top:26px;font-size:14px;padding:11px 16px}
.service:not(:first-child){padding-left:98px}

/* projects */
.center-head{position:absolute;left:0;width:1200px;text-align:center}
.center-head .rule{margin:14px auto 0}
.tabs{position:absolute;left:100px;top:1650px;width:1000px;display:flex;justify-content:center;gap:30px;font-size:15px;font-weight:600;color:var(--ink)}
.tabs .active{color:var(--orange)}
.tabs-line{position:absolute;left:100px;top:1690px;width:1000px}
.gallery-band{position:absolute;left:0;top:1750px;width:1200px;height:420px;background:var(--grey)}
.gallery{position:absolute;left:0;top:1782px;width:1200px;height:303px;display:flex}
.gallery div{width:300px;height:303px}
.all-projects{position:absolute;left:100px;top:2118px;font-size:15px;font-weight:700;color:var(--blue);letter-spacing:.5px}

/* testimonials */
.testimonial{position:absolute;top:2418px;width:480px;height:182px;background:var(--white);box-shadow:0 2px 8px rgba(0,0,0,.2);padding:62px 16px 0 16px}
.avatar{position:absolute;top:2378px;width:102px;height:102px;border-radius:50%;border:4px solid var(--orange)}
.quote-mark{position:absolute;top:2442px;font-size:44px;font-weight:700;color:var(--orange);line-height:1}
.testimonial p{font-size:13.4px;line-height:1.7}
.testimonial .who{color:var(--orange);font-weight:600;margin-top:12px;font-size:14px}

/* partners */
.partners{position:absolute;left:0;top:2760px;width:1200px;height:310px;background:var(--blue)}
.partner-row{position:absolute;left:100px;top:2842px;width:1000px;display:flex;justify-content:space-between}
.partner{width:232px;height:88px;background:var(--white);display:flex;align-items:center;justify-content:center;font-weight:700;font-size:20px;color:var(--blue)}

/* footer */
.site-footer{position:absolute;left:0;top:3040px;width:1200px;height:389px;background:var(--dark);color:var(--white)}
.footer-brand{position:absolute;left:0;top:70px;width:1200px;text-align:center}
.footer-brand .brand-name{color:var(--white);font-size:38px}
.footer-brand .brand-sub{color:var(--white)}
.footer-contact{position:absolute;left:0;top:195px;width:1200px;display:flex;justify-content:center;gap:34px;font-size:15px;font-weight:500}
.footer-nav{position:absolute;left:0;top:250px;width:1200px;display:flex;justify-content:center;gap:22px;font-size:15px;font-weight:500}
.footer-line{position:absolute;left:100px;top:308px;width:1000px;height:1px;background:#777}
.copyright{position:absolute;left:0;top:343px;width:1200px;text-align:center;font-size:15px}
</style>
</head>
<body>

<header class="site-header">
  <div class="brand">
    <div class="brand-mark"></div>
    <div>
      <div class="brand-name">BFB</div>
      <div class="brand-sub">BARLOW · BUILDING</div>
    </div>
  </div>
  <div class="topbar">
    <span><svg width="16" height="12" viewBox="0 0 16 12"><rect x="1" y="1" width="14" height="10" fill="none" stroke="#fff" stroke-width="1.5"/><path d="M1 1l7 6 7-6" fill="none" stroke="#fff" stroke-width="1.5"/></svg>Mail: info@barlowfabrication.example</span>
    <span><svg width="14" height="14" viewBox="0 0 14 14"><path d="M3 1l3 3-2 2c1 2 2 3 4 4l2-2 3 3-2 2C6 13 1 8 1 3z" fill="#fff"/></svg>Ph No: 07700900412</span>
  </div>
  <nav class="mainnav">
    <a>HOME</a><a>ABOUT US</a><a>CONSTRUCTION</a><a>OUR PROJECTS</a><a>BLOG</a><a>CONTACT US</a>
  </nav>
</header>

<section class="hero">
  <div class="hero-photo" role="img" aria-label="Steel bridge arches under construction with cranes against a blue sky"></div>
  <h1>Barlow Fabrication &amp; Building</h1>
  <p>Barlow Fabrication &amp; Building has over 15years experience working in the civil construction industry.</p>
  <a class="btn">Read More</a>
  <svg class="hero-arrow" style="left:34px" width="24" height="48" viewBox="0 0 24 48"><path d="M22 2L2 24l20 22" fill="none" stroke="#fff" stroke-width="3"/></svg>
  <svg class="hero-arrow" style="right:34px" width="24" height="48" viewBox="0 0 24 48"><path d="M2 2l20 22L2 46" fill="none" stroke="#fff" stroke-width="3"/></svg>
</section>
<svg class="abs" style="left:0;top:560px" width="1200" height="130" viewBox="0 0 1200 130">
  <polygon points="0,40 600,120 1200,0 1200,130 0,130" fill="#0655a3"/>
  <polygon points="600,120 1200,14 1200,130 0,130 0,54" fill="#f37122"/>
  <polygon points="0,68 600,130 1200,30 1200,130 0,130" fill="#fff"/>
</svg>

<section class="about">
  <div class="eyebrow">ABOUT</div>
  <h2 class="section-title" style="margin-top:6px">BARLOW FABRICATION</h2>
  <div class="rule" style="margin-top:12px"></div>
  <div class="about-text">
    <p>Barlow Fabrication &amp; Building has over 15years experience working in the civil construction industry. We are currently working on the Corran Shoreline project in London. We are subcontracted to Harlan Stroud Joint Venture and provide a highly skilled workforce across many of the Corran Shoreline sites.</p>
    <p>We have a strong history in the piling industry both in the UK and in Australia. Notable projects include working on K7 and K10 Coal Berths with Stroud Civil and Kestrel Bridge over the Wendle River for Ashford Bridgeworks in NSW Australia.</p>
  </div>
  <div class="about-bar" style="top:10px"></div>
  <div class="about-photo" role="img" aria-label="Piling barge with a crane on a river"></div>
</section>

<section class="services">
  <div class="service">
    <svg class="service-icon" width="56" height="48" viewBox="0 0 56 48"><path d="M6 34a22 22 0 0 1 44 0z" fill="#fff"/><rect x="2" y="34" width="52" height="6" fill="#fff"/><rect x="25" y="8" width="6" height="26" fill="#f37122"/></svg>
    <h3>Stadium<br><b>Construction</b></h3>
    <p>Barlow Fabrication &amp; Building has over 15years experience working in the civil construction industry.</p>
    <a class="btn">Read More</a>
  </div>
  <div class="service">
    <svg class="service-icon" width="56" height="56" viewBox="0 0 56 56"><rect x="20" y="2" width="6" height="44" fill="#fff"/><path d="M23 6L50 14" stroke="#fff" stroke-width="3"/><rect x="6" y="46" width="44" height="8" fill="#fff"/></svg>
    <h3>Gas And<br><b>Piling Works</b></h3>
    <p>Barlow Fabrication &amp; Building has over 15years experience working in the civil construction industry.</p>
    <a class="btn">Read More</a>
  </div>
  <div class="service">
    <svg class="service-icon" width="56" height="48" viewBox="0 0 56 48"><path d="M4 44V24a24 20 0 0 1 48 0v20h-10V26a14 12 0 0 0-28 0v18z" fill="#fff"/></svg>
    <h3>Bridges And<br><b>Tunnels</b></h3>
    <p>Barlow Fabrication &amp; Building has over 15years experience working in the civil construction industry.</p>
    <a class="btn">Read More</a>
  </div>
</section>

<div class="center-head" style="top:1522px">
  <div class="eyebrow">OUR</div>
  <h2 class="section-title" style="margin-top:4px">RECENT PROJECTS</h2>
</div>
<nav class="tabs">
  <span>TUNNELLING</span><span>CONVEYORS</span><span>STADIUM CONSTRUCTION</span><span class="active">GAS AND PILING</span><span>BRIDGES AND TUNNELS</span>
</nav>
<svg class="tabs-line" width="1000" height="16" viewBox="0 0 1000 16"><path d="M0 1H628l10 12 10-12H1000" fill="none" stroke="#f37122" stroke-width="2"/></svg>

<div class="gallery-band"></div>
<div class="gallery">
  <div role="img" aria-label="Inside a steel tunnel pipe" style="background:linear-gradient(180deg,#4d4f52,#8a8c8e 55%,#3a3b3d)"></div>
  <div role="img" aria-label="Red crawler crane on site" style="background:linear-gradient(180deg,#b8cbe0,#8fa6bd 50%,#6d5a52)"></div>
  <div role="img" aria-label="Cranes at dusk over the water" style="background:linear-gradient(180deg,#7c8fa8,#a8b2bd 55%,#3b3a3a)"></div>
  <div role="img" aria-label="Piling barge on a river" style="background:linear-gradient(180deg,#9fbbd8,#c7d5e3 45%,#4a5d72 65%,#2e4258)"></div>
</div>
<div class="all-projects">ALL PROJECTS</div>
<svg class="abs" style="left:1066px;top:2116px" width="36" height="20" viewBox="0 0 36 20"><path d="M12 2L4 10l8 8M24 2l8 8-8 8" fill="none" stroke="#0655a3" stroke-width="2.5"/></svg>

<div class="center-head" style="top:2242px">
  <div class="eyebrow">OUR</div>
  <h2 class="section-title" style="margin-top:4px">CLIENT TESTIMONIALS</h2>
  <div class="rule"></div>
</div>

<div class="testimonial" style="left:100px">
  <p>Duis aute irure dolor in reprehenderit in voluptate velit esse cillum dolore eu fugiat nulla pariatur. Excepteur sint occaecat cupidatat non proident</p>
  <div class="who">-Tom Archer</div>
</div>
<div class="avatar" style="left:124px;background:#c98e6a" role="img" aria-label="Client portrait"></div>
<div class="quote-mark" style="left:240px">“</div>
<div class="testimonial" style="left:620px">
  <p>Duis aute irure dolor in reprehenderit in voluptate velit esse cillum dolore eu fugiat nulla pariatur. Excepteur sint occaecat cupidatat non proident</p>
  <div class="who">-Ellen Marsh</div>
</div>
<div class="avatar" style="left:646px;background:#b5734e" role="img" aria-label="Client portrait"></div>
<div class="quote-mark" style="left:762px">“</div>

<section class="partners" role="img" aria-label="Blue band with an industrial skyline silhouette"></section>
<div class="partner-row">
  <div class="partner"><span>Ashford Bridgeworks</span></div>
  <div class="partner"><span>Corvane</span></div>
  <div class="partner"><span>Fenmore</span></div>
  <div class="partner"><span>Redlake</span></div>
</div>
<svg class="abs" style="left:34px;top:2866px" width="20" height="40" viewBox="0 0 20 40"><path d="M18 2L2 20l16 18" fill="none" stroke="#fff" stroke-width="3"/></svg>
<svg class="abs" style="left:1146px;top:2866px" width="20" height="40" viewBox="0 0 20 40"><path d="M2 2l16 18L2 38" fill="none" stroke="#fff" stroke-width="3"/></svg>

<footer class="site-footer">
  <div class="footer-brand">
    <div class="brand-name">BFB</div>
    <div class="brand-sub">BARLOW · BUILDING</div>
  </div>
  <div class="footer-contact">
    <span>✉ Mail: info@barlowfabrication.example</span>
    <span>☎ Ph No: 07700900412</span>
  </div>
  <nav class="footer-nav">
    <a>HOME</a><span>|</span><a>ABOUT US</a><span>|</span><a>CONSTRUCTION</a><span>|</span><a>OUR PROJECTS</a><span>|</span><a>BLOG</a><span>|</span><a>CONTACT US</a>
  </nav>
  <div class="footer-line"></div>
  <div class="copyright">Copyrights @ 2018 Barlow Fabrication &amp; Building. All Rights Reserved.</div>
</footer>
<svg class="abs" style="left:0;top:2980px" width="1200" height="80" viewBox="0 0 1200 80">
  <polygon points="0,80 600,4 1200,80" fill="#2b2b2b"/>
  <polygon points="600,4 1200,40 1200,62" fill="#f37122"/>
  <polygon points="0,62 600,4 0,40" fill="#fff"/>
</svg>

</body>
</html>
```